Design a New Business Card for Our Company

We are looking for fresh, unique, and a modern business card that reflects our roots as digital marketing agency focused on SEM.

Industry/Entity Type

Marketing

Contact Information for Business Card

looking for very unique out of the box designs. clean and modern that compliments our logo

Requirements
Must have
• colors should match our logo
• Front should have name, address, email, and phone/fax of the person, phone/fax are the same number
• back should have our url

```html
<!DOCTYPE html>
<html lang="en">
<head>
<meta charset="utf-8">
<title>Quilbrenna Solutions — Business Card</title>
<link href="https://fonts.googleapis.com/css2?family=Open+Sans:wght@400;600;700&display=swap" rel="stylesheet">
<style>
  :root {
    --page-bg: #e9e7e4;
    --band-blue: #5f9bd5;
    --body-white: #f4f5f7;
    --footer-grey: #b4b4b4;
    --ink: #111111;
    --text-dark: #222222;
    --accent-blue: #5b9bd5;
  }
  * { box-sizing: border-box; margin: 0; padding: 0; }
  html, body {
    width: 1200px;
    height: 900px;
    overflow: hidden;
    background: var(--page-bg);
    font-family: "Open Sans", Arial, sans-serif;
  }
  .business-card {
    position: absolute;
    left: 160px;
    top: 177px;
    width: 880px;
    height: 546px;
    display: flex;
    flex-direction: column;
    box-shadow: 0 10px 30px rgba(0,0,0,0.15);
  }
  .brand-band {
    height: 235px;
    background: var(--band-blue);
    display: flex;
    align-items: center;
    justify-content: center;
    gap: 22px;
  }
  .brand-dot {
    width: 70px;
    height: 70px;
    border-radius: 50%;
    background: var(--ink);
    flex: none;
  }
  .brand-name {
    font-weight: 700;
    font-size: 62px;
    color: var(--ink);
    letter-spacing: -1px;
    white-space: nowrap;
  }
  .contact-panel {
    height: 233px;
    background: var(--body-white);
    display: flex;
    justify-content: space-between;
    align-items: flex-start;
    padding: 58px 60px 0 60px;
  }
  .person-name {
    font-size: 35px;
    font-weight: 600;
    color: var(--accent-blue);
    line-height: 1.1;
  }
  .person-title {
    font-size: 26px;
    color: var(--text-dark);
    margin-top: 6px;
  }
  .person-address {
    font-size: 23px;
    color: var(--text-dark);
    line-height: 1.22;
    margin-top: 12px;
  }
  .contact-list {
    list-style: none;
    margin-top: 6px;
  }
  .contact-item {
    display: flex;
    justify-content: flex-end;
    align-items: center;
    gap: 12px;
    font-size: 23px;
    color: var(--text-dark);
    line-height: 31px;
  }
  .contact-icon {
    width: 16px;
    height: 16px;
    fill: var(--accent-blue);
    flex: none;
  }
  .web-footer {
    flex: 1;
    background: var(--footer-grey);
    display: flex;
    align-items: center;
    justify-content: center;
    font-weight: 700;
    font-size: 22px;
    color: var(--ink);
  }
</style>
</head>
<body>
  <div class="business-card">
    <header class="brand-band">
      <span class="brand-dot"></span>
      <span class="brand-name">Quilbrenna Solutions</span>
    </header>

    <section class="contact-panel">
      <div class="person-details">
        <p class="person-name">Daniel Carter</p>
        <p class="person-title">Managing Director</p>
        <p class="person-address">1234, Address Goes Here<br>Country Name, 123456</p>
      </div>
      <ul class="contact-list">
        <li class="contact-item">123-456-7890
          <svg class="contact-icon" viewBox="0 0 16 16" aria-hidden="true"><rect x="4" y="1" width="8" height="14" rx="1.5"/><rect x="5.5" y="3" width="5" height="8" fill="#f4f5f7"/></svg>
        </li>
        <li class="contact-item">123-456-7890
          <svg class="contact-icon" viewBox="0 0 16 16" aria-hidden="true"><path d="M1 6c0-2 3-3 7-3s7 1 7 3v1h-3V5.5H4V7H1z"/><rect x="3" y="8" width="10" height="6" rx="1"/></svg>
        </li>
        <li class="contact-item">123-456-7890
          <svg class="contact-icon" viewBox="0 0 16 16" aria-hidden="true"><rect x="4" y="1" width="8" height="5"/><rect x="1" y="6" width="14" height="9" rx="1"/><rect x="4" y="9" width="8" height="3" fill="#f4f5f7"/></svg>
        </li>
        <li class="contact-item">info@youremail.com
          <svg class="contact-icon" viewBox="0 0 16 16" aria-hidden="true"><rect x="1" y="3" width="14" height="10"/><path d="M1 3l7 6 7-6" fill="none" stroke="#f4f5f7" stroke-width="1.4"/></svg>
        </li>
      </ul>
    </section>

    <footer class="web-footer">www.quilbrenna-example.com</footer>
  </div>
</body>
</html>
```